New web page, 2 companies on the one page

A new web page for an engineering consultancy and maintenance management company

Corlett & Associates is the parent company covering the design and consultancy
Valtrix Engineering is the Maintenance and Reliability company

Target Market(s)

Food & Beverage, ingredients Manufacturing
engineering managers

Coding

Coded - Design and coding required

Number of Pages Required

1 page

Font styles to use
Other font styles liked:
• Roboto

Colors
1861ab
85acd3
d0dfed
cee9f5

```html
<!DOCTYPE html>
<html lang="en">
<head>
<meta charset="utf-8">
<title>Corlett &amp; Associates</title>
<link href="https://fonts.googleapis.com/css2?family=Barlow+Condensed:wght@400;500&family=Bebas+Neue&family=Roboto:wght@400;500;700&display=swap" rel="stylesheet">
<style>
:root{
  --navy:#1b2a44;
  --ink:#111218;
  --accent:#85acd3;
  --brand:#1861ab;
  --cyan:#12a3de;
  --grey:#7c7d80;
  --pale:#d0dfed;
  --ice:#cee9f5;
  --dark:#2a2936;
  --text:#2c2c2c;
  --white:#ffffff;
}
*{margin:0;padding:0;box-sizing:border-box}
html,body{width:1200px;height:4061px;overflow:hidden;background:var(--white)}
body{position:relative;font-family:"Roboto",sans-serif;color:var(--text)}
.abs{position:absolute}
.display{font-family:"Bebas Neue",sans-serif;letter-spacing:1px}

/* header & hero */
.hero-photo{left:0;top:0;width:1200px;height:760px;background:linear-gradient(135deg,#2c3f5e 0%,#1c2b45 45%,#13203a 100%)}
.hero-shape{left:0;top:560px}
.brand-mark{left:110px;top:24px;display:flex;align-items:center;gap:12px;color:var(--white);font-family:"Bebas Neue",sans-serif;font-size:27px;letter-spacing:1.5px;white-space:nowrap}
.brand-mark .sq{width:40px;height:40px;background:var(--white)}
.nav-item{top:28px;font-size:15px;color:var(--white);letter-spacing:.5px;white-space:nowrap}
.nav-item.active{color:var(--accent)}
.call{left:997px;top:0;width:203px;height:71px;background:var(--accent);color:var(--white);padding:10px 0 0 62px;white-space:nowrap}
.call small{display:block;font-size:12px;letter-spacing:1px}
.call strong{font-size:18px;letter-spacing:1.2px}
.call svg{position:absolute;left:16px;top:20px}
.hero-title{left:0;width:1200px;top:245px;text-align:center;color:var(--white);font-size:96px;letter-spacing:3px}
.btn{display:flex;align-items:center;height:45px;background:var(--accent);color:var(--white);font-weight:700;font-size:15px;letter-spacing:1px;padding-left:12px}
.btn .arrow{margin-left:auto;width:45px;height:45px;background:var(--white);border:2px solid var(--accent);display:flex;align-items:center;justify-content:center}
.hero-btn{left:516px;top:361px;width:169px}
.slide-arrow{top:330px;width:62px;height:62px;border:2px solid var(--white);border-radius:50%;display:flex;align-items:center;justify-content:center}

/* about */
.about-mark{left:150px;top:850px;width:410px;height:415px;display:flex;flex-direction:column;align-items:center;justify-content:center;gap:24px}
.about-mark .sq{width:150px;height:150px;background:var(--cyan)}
.about-mark span{font-family:"Bebas Neue",sans-serif;font-size:46px;color:var(--ink);letter-spacing:2px;white-space:nowrap}
.section-head{font-size:44px;color:var(--ink)}
.section-head em{font-style:normal;color:var(--accent)}
.about-head{left:627px;top:808px}
.about-text{left:627px;top:888px;width:460px;font-size:16.5px;line-height:26px}
.about-text p{margin-bottom:26px}
.about-btn{left:627px;top:1220px;width:169px}

/* services */
.services{left:0;top:1350px}
.services-title{left:0;width:1200px;top:1445px;text-align:center;font-size:44px;color:var(--ink)}
.rule{height:4px;background:var(--ink)}
.svc-label{font-family:"Bebas Neue",sans-serif;font-size:17px;line-height:22px;color:var(--ink);letter-spacing:.5px}
.center-name{left:380px;top:1945px;width:440px;text-align:center;font-family:"Bebas Neue",sans-serif;font-size:44px;color:var(--ink);letter-spacing:3px;white-space:nowrap}

/* blog */
.blog-head{left:0;width:1200px;top:2230px;text-align:center}
.card{top:2347px;width:297px;height:381px;background:var(--white);box-shadow:0 2px 10px rgba(0,0,0,.15)}
.card .photo{height:181px}
.card h3{font-size:17.5px;font-weight:700;margin:16px 14px 10px;color:var(--ink)}
.card p{font-size:15px;line-height:22px;margin:0 14px;color:#444}
.card a{display:block;margin:16px 17px;font-size:13px;font-weight:700;color:var(--accent);text-decoration:underline;letter-spacing:.5px}
.blog-btn{left:516px;top:2760px;width:169px}

/* contact */
.contact-bg{left:0;top:2894px}
.contact-title{left:0;width:1200px;top:3012px;text-align:center;color:var(--white);font-size:44px}
.info{left:110px;color:var(--white);font-size:22px;font-family:"Barlow Condensed",sans-serif;letter-spacing:.5px}
.info .label{color:var(--accent);font-size:24px;font-family:"Bebas Neue",sans-serif;letter-spacing:1px}
.info-text{position:absolute;left:76px;width:320px;line-height:34px}
.field{background:var(--white);height:50px;font-size:14px;color:#999;display:flex;align-items:center;padding-left:36px;position:absolute}
.field svg{position:absolute;left:12px}
.submit{left:547px;top:3466px;width:169px}

/* footer */
.foot-brand{left:110px;top:3750px;display:flex;align-items:center;gap:14px;font-family:"Bebas Neue",sans-serif;font-size:38px;color:var(--ink);letter-spacing:2px;white-space:nowrap}
.foot-brand .sq{width:62px;height:62px;background:var(--accent)}
.social{top:3894px;width:50px;height:50px;border-radius:50%;background:var(--accent)}
.col{top:3752px}
.col h4{font-family:"Bebas Neue",sans-serif;font-size:24px;color:var(--accent);letter-spacing:1px;font-weight:400;margin-bottom:18px}
.col li{list-style:none;font-size:12.5px;letter-spacing:1px;line-height:28px;color:var(--ink)}
.foot-rule{left:110px;top:3990px;width:980px;height:1px;background:#bbb}
.copy{top:4018px;font-size:12.5px;color:var(--ink);letter-spacing:.5px}
</style>
</head>
<body>

<!-- HERO -->
<div class="abs hero-photo" role="img" aria-label="Engineers reviewing technical plans on a computer screen in an office"></div>
<svg class="abs hero-shape" width="1200" height="200" viewBox="0 560 1200 200">
  <polygon points="0,591 591,718 591,754 0,631" fill="var(--grey)"/>
  <polygon points="610,710 1200,591 1200,631 610,754" fill="var(--cyan)"/>
  <polygon points="0,631 591,754 610,754 1200,631 1200,760 0,760" fill="#fff"/>
</svg>

<div class="abs brand-mark"><div class="sq"></div>Corlett &amp; Associates</div>
<span class="abs nav-item active" style="left:441px">HOME</span>
<span class="abs nav-item" style="left:533px">ABOUT US</span>
<span class="abs nav-item" style="left:653px">SERVICES</span>
<span class="abs nav-item" style="left:773px">TESTIMONIALS</span>
<span class="abs nav-item" style="left:926px">BLOG</span>
<div class="abs call">
  <svg width="32" height="32" viewBox="0 0 24 24" fill="none" stroke="#fff" stroke-width="1.6"><path d="M5 3h4l2 5-2.5 1.5a11 11 0 0 0 6 6L16 13l5 2v4a2 2 0 0 1-2 2A16 16 0 0 1 3 5a2 2 0 0 1 2-2"/></svg>
  <small>CALL US</small><strong>875 555 0142</strong>
</div>

<h1 class="abs hero-title display">Corlett Associates</h1>
<div class="abs btn hero-btn">GET STARTED<span class="arrow"><svg width="24" height="12" viewBox="0 0 24 12" fill="none" stroke="var(--accent)" stroke-width="2"><path d="M0 6h22M17 1l5 5-5 5"/></svg></span></div>
<div class="abs slide-arrow" style="left:28px"><svg width="22" height="14" viewBox="0 0 22 14" fill="none" stroke="#fff" stroke-width="2"><path d="M22 7H2M7 1L1 7l6 6"/></svg></div>
<div class="abs slide-arrow" style="left:1107px"><svg width="22" height="14" viewBox="0 0 22 14" fill="none" stroke="#fff" stroke-width="2"><path d="M0 7h20M15 1l6 6-6 6"/></svg></div>

<!-- ABOUT -->
<div class="abs about-mark"><div class="sq"></div><span>Corlett &amp; Associates</span></div>
<h2 class="abs section-head display about-head"><em>About</em> Us</h2>
<div class="abs about-text">
  <p>Corlett &amp; Associates is specialised manufacturing engineering support organisation that can provide fast, nimble, and flexible services.</p>
  <p>We have a proven track record in delivering tangible outcomes in process design and fit-out, project management, manufacturing process and maintenance design and execution.</p>
  <p>Our specialist focus in food manufacturing across a range of sectors allows our team to deliver real benefits to performance and recognition of the clients investment</p>
</div>
<div class="abs btn about-btn">READ MORE<span class="arrow"><svg width="24" height="12" viewBox="0 0 24 12" fill="none" stroke="var(--accent)" stroke-width="2"><path d="M0 6h22M17 1l5 5-5 5"/></svg></span></div>

<!-- SERVICES -->
<svg class="abs services" width="1200" height="810" viewBox="0 1350 1200 810">
  <defs>
    <linearGradient id="svcBg" x1="0" y1="0" x2="1" y2="1">
      <stop offset="0" stop-color="#c5dbe8"/><stop offset="1" stop-color="#d9eaf4"/>
    </linearGradient>
  </defs>
  <polygon role="img" aria-label="Faint engineering blueprint background" points="0,1427 600,1351 1200,1427 1200,2066 600,2153 0,2066" fill="url(#svcBg)"/>
  <path d="M345 2118 A273 273 0 1 1 855 2118" fill="none" stroke="var(--ink)" stroke-width="3"/>
  <g fill="var(--ink)">
    <circle cx="600" cy="1747" r="5"/><circle cx="490" cy="1770" r="5"/><circle cx="710" cy="1770" r="5"/>
    <circle cx="410" cy="1826" r="5"/><circle cx="790" cy="1826" r="5"/>
    <circle cx="360" cy="1903" r="5"/><circle cx="845" cy="1903" r="5"/>
    <circle cx="328" cy="1995" r="5"/><circle cx="872" cy="1995" r="5"/>
  </g>
  <g stroke="var(--ink)" stroke-width="1.5" stroke-dasharray="5 4" fill="none">
    <path d="M600 1700V1747"/><path d="M460 1727L490 1770"/><path d="M742 1727L710 1770"/>
    <path d="M375 1795L410 1826"/><path d="M830 1798L790 1826"/>
    <path d="M318 1885L360 1903"/><path d="M885 1885L845 1903"/>
    <path d="M298 2000H328"/><path d="M905 2000H872"/>
  </g>
  <g fill="#fff" stroke="var(--ink)" stroke-width="2.5">
    <polygon points="449,1659 482,1677 482,1713 449,1731 416,1713 416,1677"/>
    <polygon points="752,1659 785,1677 785,1713 752,1731 719,1713 719,1677"/>
    <polygon points="347,1738 380,1756 380,1792 347,1810 314,1792 314,1756"/>
    <polygon points="859,1738 892,1756 892,1792 859,1810 826,1792 826,1756"/>
    <polygon points="284,1837 317,1855 317,1891 284,1909 251,1891 251,1855"/>
    <polygon points="918,1837 951,1855 951,1891 918,1909 885,1891 885,1855"/>
    <polygon points="263,1967 296,1985 296,2021 263,2039 230,2021 230,1985"/>
    <polygon points="940,1967 973,1985 973,2021 940,2039 907,2021 907,1985"/>
  </g>
  <polygon points="600,1631 634,1649 634,1685 600,1703 566,1685 566,1649" fill="var(--ink)"/>
  <g fill="none" stroke="var(--ink)" stroke-width="1.8">
    <rect x="437" y="1685" width="24" height="16"/><path d="M441 1697l6-6 4 3 6-6"/>
    <path d="M745 1706l12-16 4 4-16 12zM745 1706l-3 4"/>
    <rect x="335" y="1763" width="24" height="22"/><path d="M340 1770h14M340 1776h14"/>
    <rect x="847" y="1764" width="24" height="20"/><path d="M852 1770h14M852 1776h10"/>
    <rect x="272" y="1862" width="24" height="22"/><path d="M277 1878v-6M283 1878v-10M289 1878v-4"/>
    <rect x="908" y="1862" width="20" height="22"/><path d="M912 1869h12M912 1875h12M912 1881h8"/>
    <circle cx="255" cy="1995" r="4"/><circle cx="272" cy="2011" r="4"/><path d="M259 1995h10v12"/>
    <circle cx="940" cy="2003" r="11"/><circle cx="940" cy="2003" r="4"/>
  </g>
  <g fill="none" stroke="#fff" stroke-width="1.8">
    <rect x="589" y="1654" width="22" height="26"/><path d="M593 1662h14M593 1668h14M593 1674h10"/>
  </g>
</svg>
<h2 class="abs services-title display">Our Services</h2>
<div class="abs rule" style="left:550px;top:1507px;width:100px"></div>

<div class="abs svc-label" style="left:500px;width:200px;top:1570px;text-align:center">Maintenance<br>Execution</div>
<div class="abs svc-label" style="left:203px;width:220px;top:1626px;text-align:right">Engineering &amp; Maintenance<br>Management</div>
<div class="abs svc-label" style="left:779px;top:1626px">Manufacturing Performance<br>Measurement</div>
<div class="abs svc-label" style="left:81px;width:220px;top:1740px;text-align:right">Major Equipment &amp; Services<br>Installation &amp; Commissioning</div>
<div class="abs svc-label" style="left:902px;top:1750px">SCADA</div>
<div class="abs svc-label" style="left:100px;width:140px;top:1848px;text-align:right">Project<br>Management</div>
<div class="abs svc-label" style="left:963px;top:1844px">Vision Inspection<br>Systems</div>
<div class="abs svc-label" style="left:73px;width:140px;top:1973px;text-align:right">Process &amp;<br>Facilities Design</div>
<div class="abs svc-label" style="left:979px;top:1973px">Acquisition Due<br>Diligence</div>
<div class="abs center-name">Corlett &amp; Associates</div>

<!-- BLOG -->
<h2 class="abs section-head display blog-head"><em>Blog &amp;</em> News</h2>
<div class="abs rule" style="left:550px;top:2291px;width:100px;background:var(--accent)"></div>

<article class="abs card" style="left:110px">
  <div class="photo" role="img" aria-label="Engineer in a hard hat using a tablet on a factory floor" style="background:linear-gradient(135deg,#5f6f7c,#2f3d4a)"></div>
  <h3>Deatae Eitaeictaunt Explicabo</h3>
  <p>Perspiciatis unde omnis iste natus error sit voluptatem accusantium doloremque laudantium totak mserremlo reseos qui.</p>
  <a>READ MORE</a>
</article>
<article class="abs card" style="left:451px">
  <div class="photo" role="img" aria-label="Engineer working on 3D machine part designs across computer monitors" style="background:linear-gradient(135deg,#8fa3b8,#3a4656)"></div>
  <h3>Daonsequuntur Magnidolores</h3>
  <p>Perspiciatis unde omnis iste natus error sit voluptatem accusantium doloremque laudantium totak mserremlo reseos qui.</p>
  <a>READ MORE</a>
</article>
<article class="abs card" style="left:792px">
  <div class="photo" role="img" aria-label="Two engineers reviewing data at a workstation in a laboratory" style="background:linear-gradient(135deg,#c9d2da,#6e7c8a)"></div>
  <h3>Suikatione Eoluptatem lequi</h3>
  <p>Perspiciatis unde omnis iste natus error sit voluptatem accusantium doloremque laudantium totak mserremlo reseos qui.</p>
  <a>READ MORE</a>
</article>
<div class="abs btn blog-btn">VIEW MORE<span class="arrow"><svg width="24" height="12" viewBox="0 0 24 12" fill="none" stroke="var(--accent)" stroke-width="2"><path d="M0 6h22M17 1l5 5-5 5"/></svg></span></div>

<!-- CONTACT -->
<svg class="abs contact-bg" width="1200" height="775" viewBox="0 2894 1200 775">
  <defs>
    <linearGradient id="ctBg" x1="0" y1="0" x2="1" y2="1">
      <stop offset="0" stop-color="#3a3946"/><stop offset="1" stop-color="#22212c"/>
    </linearGradient>
  </defs>
  <polygon role="img" aria-label="Dim industrial plant with an engineer pointing, darkened background" points="0,2970 600,2894 1200,2970 1200,3596 600,3667 0,3596" fill="url(#ctBg)"/>
</svg>
<h2 class="abs contact-title display">Contact Us</h2>
<div class="abs rule" style="left:538px;top:3072px;width:124px;background:var(--white)"></div>

<div class="abs info" style="top:3160px">
  <svg width="34" height="42" viewBox="0 0 24 30" fill="var(--accent)" style="position:absolute;left:4px;top:2px"><path d="M12 0a11 11 0 0 0-11 11c0 8 11 19 11 19s11-11 11-19A11 11 0 0 0 12 0zm0 15a4 4 0 1 1 0-8 4 4 0 0 1 0 8z"/></svg>
  <div class="info-text">12 Harbour Rd, Eastfield, NSW<br>2290.</div>
</div>
<div class="abs info" style="top:3258px">
  <svg width="40" height="28" viewBox="0 0 40 28" style="position:absolute;left:0;top:12px"><rect width="40" height="28" fill="var(--accent)"/><path d="M0 0l20 16L40 0" fill="none" stroke="var(--dark)" stroke-width="2"/></svg>
  <div class="info-text"><span class="label">General Enquiries:</span><br>hello@corlettassoc.com</div>
</div>
<div class="abs info" style="top:3352px">
  <svg width="34" height="34" viewBox="0 0 24 24" fill="var(--accent)" style="position:absolute;left:4px;top:14px"><path d="M5 2h4l2 6-3 2a12 12 0 0 0 6 6l2-3 6 2v4a2 2 0 0 1-2 2A19 19 0 0 1 3 4a2 2 0 0 1 2-2z"/></svg>
  <div class="info-text"><span class="label">Phone</span><br>875 555 0142</div>
</div>

<div class="field" style="left:547px;top:3138px;width:254px"><svg width="14" height="14" viewBox="0 0 14 14" fill="var(--accent)"><circle cx="7" cy="4" r="3.5"/><path d="M0 14a7 6 0 0 1 14 0z"/></svg>First Name</div>
<div class="field" style="left:833px;top:3138px;width:254px"><svg width="14" height="14" viewBox="0 0 14 14" fill="var(--accent)"><circle cx="7" cy="4" r="3.5"/><path d="M0 14a7 6 0 0 1 14 0z"/></svg>Last Name</div>
<div class="field" style="left:547px;top:3216px;width:254px"><svg width="14" height="14" viewBox="0 0 24 24" fill="var(--accent)"><path d="M5 2h4l2 6-3 2a12 12 0 0 0 6 6l2-3 6 2v4a2 2 0 0 1-2 2A19 19 0 0 1 3 4a2 2 0 0 1 2-2z"/></svg>Enter Phone</div>
<div class="field" style="left:833px;top:3216px;width:254px"><svg width="16" height="11" viewBox="0 0 16 11"><rect width="16" height="11" fill="var(--accent)"/><path d="M0 0l8 6 8-6" fill="none" stroke="#fff"/></svg>Enter Email</div>
<div class="field" style="left:547px;top:3293px;width:540px;height:153px;align-items:flex-start;padding-top:14px"><svg width="14" height="14" viewBox="0 0 14 14" style="top:14px" fill="none" stroke="var(--accent)" stroke-width="2"><path d="M1 1l12 12"/></svg>Enter Message</div>
<div class="abs btn submit">SUBMIT<span class="arrow"><svg width="24" height="12" viewBox="0 0 24 12" fill="none" stroke="var(--accent)" stroke-width="2"><path d="M0 6h22M17 1l5 5-5 5"/></svg></span></div>

<!-- FOOTER -->
<div class="abs foot-brand"><div class="sq"></div>Valtrix Engineering</div>
<div class="abs social" style="left:215px" aria-label="Social link 1"></div>
<div class="abs social" style="left:290px" aria-label="Social link 2"></div>
<div class="abs social" style="left:365px" aria-label="Social link 3"></div>

<div class="abs col" style="left:541px"><h4>Quick Links</h4><ul><li>HOME</li><li>ABOUT US</li><li>SERVICES</li><li>TESTIMONIALS</li><li>BLOG</li></ul></div>
<div class="abs col" style="left:766px"><h4>Links</h4><ul><li>FAQ</li><li>TERMS &amp; CONDITIONS</li><li>PRIVACY POLICY</li><li>SITE MAP</li></ul></div>
<div class="abs col" style="left:1001px"><h4>Support</h4><ul><li>TEAM</li><li>ABOUT US</li><li>CAREERS</li><li>OUR VALUES</li></ul></div>

<div class="abs foot-rule"></div>
<div class="abs copy" style="left:110px">Copyright © 2021.&nbsp; All rights reserved</div>
<div class="abs copy" style="left:866px">Privacy Policy</div>
<div class="abs" style="left:970px;top:4008px;width:1px;height:34px;background:#bbb"></div>
<div class="abs copy" style="left:993px">Cookies Policy</div>

</body>
</html>
```